Web Design Project and logo

We need a new web design and logo for www.kz7ventures.com

It is a mobile app development company. Site needs to look very cool/trendy as does the new logo.

Looking for the design (uncoded) and the logo file that my developers can then use to build out the site.

An example of a nice competitor site is www.thecodegarage.com

We want something that looks fresh, clean and hip.

Also development of business cards.

Target Market(s)

Small to mid sized companies

Industry/Entity Type

Business

Requirements
Must have
• Ability to request a quote
Should look very trendy like www.thecodegarage.com as an example of a competitor site

```html
<!DOCTYPE html>
<html lang="en">
<head>
<meta charset="utf-8">
<title>KZ7 Ventures — Mobile App Development</title>
<link rel="stylesheet" href="https://fonts.googleapis.com/css2?family=Open+Sans:wght@300;400;600&display=swap">
<style>
  :root {
    --accent: #f4503c;
    --accent-dark: #d83e2b;
    --header-bg: #ffffff;
    --nav-text: #6b6b6b;
    --nav-active: #2b2b2b;
    --divider: #e3e3e3;
    --button-grey: #d9d9d9;
    --button-grey-text: #ffffff;
    --hero-dark: #0b0b0e;
    --caption-bg: rgba(20, 20, 24, 0.82);
    --feature-bg: rgba(14, 34, 58, 0.78);
    --white: #ffffff;
    --soft-white: #e8ecf1;
  }
  * { box-sizing: border-box; margin: 0; padding: 0; }
  html, body {
    width: 1200px; height: 720px; overflow: hidden;
    font-family: "Open Sans", Arial, sans-serif;
    background: var(--hero-dark);
  }
  .page { position: relative; width: 1200px; height: 720px; overflow: hidden; }

  /* Header */
  .site-header {
    position: absolute; top: 0; left: 0; width: 1200px; height: 72px;
    background: var(--header-bg);
    display: flex; align-items: center;
    border-bottom: 1px solid var(--divider);
  }
  .brand {
    display: flex; align-items: center; gap: 10px;
    padding-left: 26px; width: 210px;
    color: var(--accent); font-weight: 600; font-size: 21px; letter-spacing: 0.5px;
  }
  .brand-mark { width: 14px; height: 14px; background: var(--accent); }
  .main-nav { display: flex; height: 72px; margin-left: 8px; }
  .main-nav a {
    display: flex; align-items: center; height: 100%;
    padding: 0 22px; font-size: 14px; color: var(--nav-text);
    text-decoration: none; border-left: 1px solid var(--divider);
  }
  .main-nav a:last-child { border-right: 1px solid var(--divider); }
  .main-nav a.is-active { color: var(--nav-active); }
  .header-tools { margin-left: auto; display: flex; align-items: center; height: 72px; }
  .call-us { font-size: 14px; color: var(--nav-text); padding: 0 22px; }
  .language {
    display: flex; align-items: center; gap: 8px; height: 100%;
    padding: 0 22px; font-size: 13px; color: var(--nav-text);
    border-left: 1px solid var(--divider); border-right: 1px solid var(--divider);
  }
  .quote-button {
    margin: 0 26px 0 26px; padding: 8px 12px;
    background: var(--button-grey); color: var(--button-grey-text);
    font-size: 13px; border-radius: 3px; text-decoration: none;
    box-shadow: inset 0 -2px 0 rgba(0,0,0,0.08);
  }

  /* Hero */
  .hero { position: absolute; top: 72px; left: 0; width: 1200px; height: 648px; }
  .hero-photo {
    position: absolute; inset: 0;
    background:
      radial-gradient(ellipse 380px 420px at 230px 170px, rgba(214,150,120,0.95), rgba(150,80,60,0.6) 55%, transparent 80%),
      radial-gradient(ellipse 520px 300px at 1020px 220px, rgba(200,70,40,0.85), rgba(120,30,20,0.4) 55%, transparent 85%),
      radial-gradient(ellipse 700px 220px at 700px 560px, rgba(80,110,160,0.55), transparent 75%),
      linear-gradient(180deg, #1a0f0d 0%, #0c0a0c 55%, #13151c 100%);
  }
  .hero-content { position: absolute; top: 0; left: 0; width: 1200px; text-align: center; }
  .hero-title {
    margin-top: 118px; font-weight: 300; font-size: 54px; letter-spacing: 1px;
    color: var(--white);
  }
  .hero-caption {
    display: inline-block; margin-top: 14px; padding: 6px 12px;
    background: var(--caption-bg); color: var(--soft-white);
    font-size: 14px;
  }
  .hero-actions { display: flex; justify-content: center; gap: 56px; margin-top: 40px; }
  .hero-button {
    display: inline-flex; align-items: center; justify-content: center;
    height: 58px; padding: 0 16px; background: var(--accent);
    color: var(--white); font-size: 16px; text-decoration: none;
    box-shadow: 0 3px 0 var(--accent-dark);
  }
  .hero-button.details { width: 196px; }
  .hero-button.request { width: 194px; }

  /* Feature strip */
  .features {
    position: absolute; left: 28px; top: 518px;
    display: flex; gap: 14px;
  }
  .feature {
    width: 376px; height: 102px; background: var(--feature-bg);
    display: flex; align-items: flex-start; gap: 18px; padding: 20px 18px 0 26px;
    color: var(--white);
  }
  .feature-icon { flex: 0 0 46px; height: 46px; margin-top: 6px; }
  .feature-title { font-size: 14px; text-transform: uppercase; margin-bottom: 4px; }
  .feature-text { font-size: 13.5px; line-height: 1.4; color: var(--soft-white); }
</style>
</head>
<body>
<div class="page">
  <header class="site-header">
    <div class="brand"><span class="brand-mark"></span>KZ7 Ventures</div>
    <nav class="main-nav">
      <a href="#" class="is-active">HOME</a>
      <a href="#">OUR SERVICES</a>
      <a href="#">LATEST NEWS</a>
      <a href="#">CONTACT</a>
    </nav>
    <div class="header-tools">
      <span class="call-us">CALL US ON: +00 000 0000</span>
      <span class="language">ENGLISH
        <svg width="10" height="6" viewBox="0 0 10 6"><path d="M1 1l4 4 4-4" fill="none" stroke="#6b6b6b" stroke-width="1.5"/></svg>
      </span>
      <a href="#" class="quote-button">I NEED APP NOW!</a>
    </div>
  </header>

  <section class="hero">
    <div class="hero-photo" role="img" aria-label="Close-up photo of a fingertip touching a glowing touchscreen in warm orange and dark tones"></div>
    <div class="hero-content">
      <h1 class="hero-title">THE NO1 APPS</h1>
      <p class="hero-caption">KZ7 Ventures helps you is a specialty mobile solutions provider with expertise across all the major mobile platforms.</p>
      <div class="hero-actions">
        <a href="#" class="hero-button details">SEE THE DETAILS NOW</a>
        <a href="#" class="hero-button request">I NEED APP NOW</a>
      </div>
    </div>

    <div class="features">
      <div class="feature">
        <svg class="feature-icon" viewBox="0 0 46 46" aria-hidden="true">
          <rect x="8" y="6" width="20" height="32" rx="3" fill="none" stroke="#fff" stroke-width="2.5"/>
          <rect x="22" y="16" width="16" height="24" rx="2" fill="none" stroke="#fff" stroke-width="2.5"/>
        </svg>
        <div>
          <div class="feature-title">Mobile Services</div>
          <div class="feature-text">Our comprehensive range of consulting services takes you from idea through development.</div>
        </div>
      </div>
      <div class="feature">
        <svg class="feature-icon" viewBox="0 0 46 46" aria-hidden="true">
          <path d="M23 40C10 30 4 23 4 15a9 9 0 0 1 19-4 9 9 0 0 1 19 4c0 8-6 15-19 25z" fill="#fff"/>
        </svg>
        <div>
          <div class="feature-title">Quality Through Experience</div>
          <div class="feature-text">Our team of engineers know what it takes to serve more than 1,000,000 happy customers.</div>
        </div>
      </div>
      <div class="feature">
        <svg class="feature-icon" viewBox="0 0 46 46" aria-hidden="true">
          <circle cx="23" cy="23" r="15" fill="none" stroke="#fff" stroke-width="3"/>
          <circle cx="23" cy="23" r="4" fill="#fff"/>
          <path d="M23 3v10M23 33v10M3 23h10M33 23h10" stroke="#fff" stroke-width="3"/>
        </svg>
        <div>
          <div class="feature-title">I Want You!</div>
          <div class="feature-text">KZ7 is always looking for talented developers. If you have what it takes - Do not hesitate to contact us.</div>
        </div>
      </div>
    </div>
  </section>
</div>
</body>
</html>
```